Business Card Makeover. Recreate a sleek modern design for our business card.

DO NOT COPY OUR CURRENT DESIGN. MUST BE ONE SIDED BUSINESS CARD.
Create a new business card design, using our new logo. Attached is a sample of our current design and new logo. Please note the address and email will change. The new address is 412 Corvell West Palm Beach 33401 and our website will be www.delmarhollis.example.

We are an architectural and interior design firm. We prefer a clean modern look. Something that is refined and emulates excellence.

Industry/Entity Type

Architecture

Contact Information for Business Card

clean modern look, please do not copy our attached design.

Font styles to use
Other font styles liked:
• see attached business card font

Colors

Designer to choose colors to be used in the design.

Requirements
Must have
• Must have a modern appeal and resemble our current branding.
Nice to have
• modern font, our logo, legible name and titles progressive design
Should not have
• Do not add colors not reflected in our branding. Should not look like our current card.

```html
<!DOCTYPE html>
<html lang="en">
<head>
<meta charset="utf-8">
<title>Delmar Hollis + Partners — Business Card</title>
<link rel="stylesheet" href="https://fonts.googleapis.com/css2?family=Lato:wght@300;400;700;900&display=swap">
<style>
  :root {
    --backdrop: #9c9c9c;
    --card: #262527;
    --card-edge: #1d1c1e;
    --text: #c8c8c8;
    --text-soft: #b4b4b4;
    --accent: #0a78c8;
    --rule: #3c3b3e;
  }
  * { margin: 0; padding: 0; box-sizing: border-box; }
  html, body {
    width: 1200px; height: 802px; overflow: hidden;
    background: var(--backdrop);
    font-family: "Lato", sans-serif;
  }
  .card {
    position: absolute; left: 150px; top: 131px;
    width: 900px; height: 540px;
    background: var(--card);
    box-shadow: 0 6px 18px rgba(0,0,0,.35);
    overflow: hidden;
  }
  .brand { position: absolute; right: 53px; top: 62px; text-align: right; }
  .brand-mark {
    position: absolute; left: 324px; top: 73px;
    width: 107px; height: 107px; border-radius: 50%;
    background: var(--accent);
  }
  .brand-name {
    position: absolute; left: 449px; top: 92px;
    font-size: 47px; font-weight: 300; color: #e6e6e6;
    letter-spacing: .01em; line-height: 1;
  }
  .brand-suffix {
    position: absolute; right: 53px; top: 142px;
    font-size: 14px; letter-spacing: .5em; color: var(--text);
    line-height: 1;
  }
  .tagline {
    position: absolute; left: 470px; top: 177px;
    font-size: 26px; color: var(--text-soft); line-height: 1.1;
  }
  .person-name {
    position: absolute; left: 50px; top: 250px;
    font-size: 35px; font-weight: 900; color: var(--accent);
    line-height: 1; letter-spacing: .01em;
  }
  .person-rule {
    position: absolute; left: 393px; top: 271px; width: 454px; height: 1px;
    background: var(--rule);
  }
  .person-title {
    position: absolute; left: 51px; top: 282px;
    font-size: 26px; color: var(--text-soft); line-height: 1.1;
  }
  .contact-list { position: absolute; left: 50px; top: 343px; list-style: none; }
  .contact-list li {
    display: flex; align-items: center; height: 30.2px;
    font-size: 25px; color: var(--text); line-height: 1;
  }
  .contact-list svg { width: 19px; height: 19px; margin-right: 9px; fill: var(--accent); flex: none; }
  .address {
    position: absolute; right: 53px; top: 377px; text-align: right;
    font-size: 25px; color: var(--text); line-height: 31px; font-style: normal;
  }
  .license {
    position: absolute; right: 53px; top: 467px;
    font-size: 25px; color: var(--text); line-height: 1;
  }
  .license .label { color: var(--accent); }
  .base-band {
    position: absolute; left: 0; bottom: 0; width: 100%; height: 12px;
    background: var(--accent);
  }
</style>
</head>
<body>
  <article class="card">
    <div class="brand-mark" aria-hidden="true"></div>
    <div class="brand-name">DELMARHOLLIS</div>
    <div class="brand-suffix">+ PARTNERS</div>
    <div class="tagline">Architecture + Interior Design</div>

    <h1 class="person-name">THEO MARCHETTI</h1>
    <div class="person-rule"></div>
    <p class="person-title">Partner / Director of Design</p>

    <ul class="contact-list">
      <li><svg viewBox="0 0 20 20" aria-hidden="true"><path d="M2 7c0-2 3-4 8-4s8 2 8 4v2h-4V7.5c-1-.7-2.5-1-4-1s-3 .3-4 1V9H2z"/><path d="M4 11h12l1 6H3z"/></svg>561.555.0148</li>
      <li><svg viewBox="0 0 20 20" aria-hidden="true"><path d="M6 1h8a1 1 0 0 1 1 1v16a1 1 0 0 1-1 1H6a1 1 0 0 1-1-1V2a1 1 0 0 1 1-1zm1 2v12h6V3z"/></svg>561.555.0172</li>
      <li><svg viewBox="0 0 20 20" aria-hidden="true"><path d="M5 2h10v5H5z"/><path d="M2 8h16v7h-3v-3H5v3H2z"/><path d="M6 13h8v5H6z"/></svg>561.555.0193</li>
      <li><svg viewBox="0 0 20 20" aria-hidden="true"><path d="M2 5h16v10H2z" /><path d="M2 5l8 6 8-6" fill="none" stroke="#262527" stroke-width="1.6"/></svg>theo@delmarhollis.example</li>
      <li><svg viewBox="0 0 20 20" aria-hidden="true"><circle cx="10" cy="10" r="8"/><path d="M6 6c2 0 3 2 2 3s-3 1-2 4M12 4c0 2 3 2 3 4s-2 2-1 5" fill="none" stroke="#262527" stroke-width="1.4"/></svg>www.delmarhollis.example</li>
    </ul>

    <address class="address">412 Corvell West<br>Palm Beach 33401</address>
    <p class="license"><span class="label">LIC</span> # AA26007714</p>

    <div class="base-band"></div>
  </article>
</body>
</html>
```